Brightfield Ventures Inc. Letterhead

Creation of attractive and eye catching letterhead for a business start-up for the construction industry. Letterhead must relate to construction, but avoid standard hammer and tools in the design.

I forgot to add some details, sorry about that. Some pertinent info: Ph: 916-555-0187 brightfieldventures.example 448 Willowmere Ave, Ste 210 Folsom, CA 95999 info@brightfieldventures.example not sure if slogan should be in there" “Connecting construction professionals to create a purpose driven industry.” must be able to be used in word. Thanks!

```html
<!DOCTYPE html>
<html lang="en">
<head>
<meta charset="utf-8">
<title>Brightfield Ventures Letterhead</title>
<link href="https://fonts.googleapis.com/css2?family=Lato:wght@400;700;900&family=Yellowtail&display=swap" rel="stylesheet">
<style>
  :root {
    --navy: #1c1f5c;
    --red: #c8202b;
    --ink: #4d4d52;
    --dark: #222226;
    --rule: #b9b9bf;
    --paper: #ffffff;
  }
  * { margin: 0; padding: 0; box-sizing: border-box; }
  html, body { width: 894px; height: 1200px; overflow: hidden; background: var(--paper); }
  .letterhead {
    position: relative;
    width: 894px;
    height: 1200px;
    background: var(--paper);
    font-family: "Lato", sans-serif;
    color: var(--ink);
  }
  .brand {
    position: absolute;
    left: 74px;
    top: 58px;
    display: flex;
    align-items: center;
    gap: 14px;
  }
  .brand-mark { width: 26px; height: 26px; background: var(--red); flex: none; }
  .brand-name {
    font-weight: 900;
    font-size: 24px;
    letter-spacing: 2.5px;
    text-transform: uppercase;
    color: var(--navy);
    line-height: 1.2;
  }
  .contact {
    position: absolute;
    left: 624px;
    top: 34px;
    padding-left: 12px;
    border-left: 1px solid var(--rule);
    font-size: 13.5px;
    line-height: 20px;
    color: var(--ink);
  }
  .contact-row { display: flex; align-items: flex-start; gap: 5px; white-space: nowrap; }
  .contact-row svg { width: 11px; height: 11px; margin-top: 4px; flex: none; fill: var(--red); }
  .contact-row.address { margin-bottom: 12px; }
  .letter-body {
    position: absolute;
    left: 75px;
    top: 232px;
    width: 741px;
  }
  .salutation {
    font-weight: 700;
    font-size: 17px;
    color: var(--navy);
    margin-bottom: 18px;
  }
  .paragraph {
    font-size: 17.5px;
    line-height: 27.8px;
    text-align: justify;
    hyphens: auto;
    margin-bottom: 20px;
  }
  .closing { font-size: 20px; color: var(--dark); margin-top: 30px; }
  .signature {
    font-family: "Yellowtail", cursive;
    font-size: 38px;
    line-height: 1.2;
    color: var(--navy);
    margin-top: 2px;
  }
  .footer-bands {
    position: absolute;
    left: 0;
    bottom: 0;
    width: 894px;
    height: 8px;
    display: flex;
    gap: 6px;
  }
  .band { flex: 1; }
  .band.navy { background: var(--navy); }
  .band.red { background: var(--red); }
</style>
</head>
<body>
  <div class="letterhead">
    <header>
      <div class="brand">
        <span class="brand-mark"></span>
        <span class="brand-name">Brightfield<br>Ventures Inc.</span>
      </div>
      <div class="contact">
        <div class="contact-row address">
          <svg viewBox="0 0 12 12"><path d="M6 0a4 4 0 0 0-4 4c0 3 4 8 4 8s4-5 4-8a4 4 0 0 0-4-4zm0 5.6A1.6 1.6 0 1 1 6 2.4a1.6 1.6 0 0 1 0 3.2z"/></svg>
          <span>448 Willowmere Ave, Ste 210<br>Folsom, CA 95999</span>
        </div>
        <div class="contact-row">
          <svg viewBox="0 0 12 12"><path d="M2.5 0.5l2 2.5-1.2 1.5c.7 1.6 2 2.9 3.6 3.6L8.4 6.9l2.6 2-1 2.3C5 11 1 7 .8 2z"/></svg>
          <span>Ph: 916-555-0187</span>
        </div>
        <div class="contact-row">
          <svg viewBox="0 0 12 12"><path d="M0 4l6 3.5L12 4v6H0zM0 3l6-3 6 3-6 3.4z"/></svg>
          <span>info@brightfieldventures.example</span>
        </div>
        <div class="contact-row">
          <svg viewBox="0 0 12 12"><path d="M6 0a6 6 0 1 0 0 12A6 6 0 0 0 6 0zm0 1.2c.8.8 1.4 2.4 1.5 4.2h-3C4.6 3.6 5.2 2 6 1.2zM1.3 6.6h2.2c.1 1.6.5 3 1.2 4A4.8 4.8 0 0 1 1.3 6.6zm0-1.2a4.8 4.8 0 0 1 3.4-4c-.7 1-1.1 2.4-1.2 4zm4.7 5.4c-.8-.8-1.4-2.4-1.5-4.2h3c-.1 1.8-.7 3.4-1.5 4.2zm1.3-.2c.7-1 1.1-2.4 1.2-4h2.2a4.8 4.8 0 0 1-3.4 4zm1.2-5.2c-.1-1.6-.5-3-1.2-4a4.8 4.8 0 0 1 3.4 4z"/></svg>
          <span>brightfieldventures.example</span>
        </div>
      </div>
    </header>

    <main class="letter-body">
      <p class="salutation">Dear Mr. Lorem,</p>
      <p class="paragraph">Lorem ipsum dolor sit amet, consectetuer adipiscing elit, sed diam nonummy nibh euismod tincidunt ut laoreet dolore magna aliquam erat volutpat. Ut wisi enim ad minim veniam, quis nostrud exerci tation ullamcorper suscipit lobortis nisl ut aliquip ex ea commodo consequat. Duis autem vel eum iriure dolor in hendiusto odio dignissim qui blandit praesent luptatum zzril delenit augue duis dolore te feugait nulla facilisi.</p>
      <p class="paragraph">Lorem ipsum dolor sit amet, consectetuer adipiscing elit, sed diam nonummy nibh euismod tincidunt ut laoreet dolore magna aliquam erat volutpat. Ut wisi enim ad minim veniam, quis nostrud exerci tation ullamcorper suscipit lobortis nisl ut aliquip ex ea commodo consequat. Duis autem vel eum iriure dolor in hendiusto odio dignissim qui blandit praesent luptatum zzril delenit augue duis dolore te feugait nulla facilisi.</p>
      <p class="paragraph">Lorem ipsum dolor sit amet, consectetuer adipiscing elit, sed diam nonummy nibh euismod tincidunt ut laoreet dolore magna aliquam erat volutpat. Ut wisi enim ad minim veniam, quis nostrud exerci tation ullamcorper suscipit lobortis nisl ut aliquip ex ea commodo consequat. Duis autem vel eum iriure dolor in hendiusto odio dignissim qui blandit praesent luptatum zzril delenit augue duis dolore te feugait nulla facilisi.</p>
      <p class="closing">Sincerely Your,</p>
      <p class="signature">Your Name</p>
    </main>

    <footer class="footer-bands">
      <span class="band navy"></span>
      <span class="band red"></span>
      <span class="band navy"></span>
    </footer>
  </div>
</body>
</html>
```